Lucky Harbour Fun Casino Entertainment

Looking to update my business card and make it look more modern, stand out and eye catching.
We are are fun casino business in Australia (primarily Sydney). Blackjack and Roulette are our most popular games although we have pretty much every game available for hire that you would find in a real casino. The final design would need to be sleek and appeal to the more upmarket corporate sector.
We mainly cater for Corporate Events, Private Parties, Fundraising Events, Team Building, Poker Tournaments
I think I'd prefer the colour Black.

Target Market(s)

High-end Corporate

Industry/Entity Type

Events

Contact Information for Business Card

Rob Kendall
Director
1300 482 617
0433 728 591
info@luckyharbour.com.au
www.luckyharbour.com.au
Facebook & Instagram @luckyharbourevents (proper social icons preferred)

Colors
000000
0255a3

Requirements
Must have
• Front side:
• Logo
• Contact details
• 'Australia's #1 Fun Casino Specialists'
• Back:
• Logo
Nice to have
• Back:
• Corporate Events
• Private Parties
• Poker Tournaments
• Fundraising
• Props & Theming
• Photo Booth
• Horse Racing Events
• The Vegas Sign attached, maybe on the back of the card in the background...?

```html
<!DOCTYPE html>
<html lang="en">
<head>
<meta charset="utf-8">
<title>Lucky Harbour – Business Card</title>
<link rel="stylesheet" href="https://fonts.googleapis.com/css2?family=Roboto:wght@400;500&display=swap">
<style>
  :root {
    --backdrop: #9a9a9a;
    --card: #0e0e0e;
    --card-edge: #161616;
    --gold: #f7a823;
    --text-light: #f2f2f2;
    --text-muted: #c9c9c9;
    --text-soft: #a8a8a8;
    --rule: #4a4a4a;
    --icon-ink: #111111;
  }
  * { margin: 0; padding: 0; box-sizing: border-box; }
  html, body { width: 1200px; height: 900px; overflow: hidden; }
  body {
    background: var(--backdrop);
    font-family: "Roboto", Arial, sans-serif;
    position: relative;
  }
  .card {
    position: absolute;
    background: linear-gradient(160deg, var(--card-edge), var(--card) 60%);
    box-shadow: 4px 5px 6px rgba(0,0,0,0.35);
  }
  .card--front { left: 121px; top: 275px; width: 476px; height: 295px; border-radius: 0 48px 0 48px; }
  .card--back  { left: 607px; top: 275px; width: 476px; height: 292px; border-radius: 48px 0 48px 0; }

  .brand {
    position: absolute;
    display: flex;
    align-items: center;
    gap: 8px;
    color: var(--gold);
    font-weight: 500;
    font-size: 21px;
    letter-spacing: 0.5px;
    white-space: nowrap;
  }
  .brand__dot { width: 14px; height: 14px; border-radius: 50%; background: var(--gold); flex: none; }
  .card--front .brand { left: 44px; top: 132px; }
  .card--back .brand  { left: 38px; top: 132px; }

  .divider { position: absolute; width: 1px; background: var(--rule); }
  .card--front .divider { left: 240px; top: 87px; height: 120px; }
  .card--back .divider  { left: 244px; top: 87px; height: 115px; }

  .contact-name {
    position: absolute; left: 261px; top: 81px;
    color: var(--gold); font-size: 21px; font-weight: 500; letter-spacing: 0.3px;
  }
  .contact-role {
    position: absolute; left: 261px; top: 104px;
    color: var(--text-soft); font-size: 14px;
  }
  .contact-list { position: absolute; left: 261px; top: 138px; list-style: none; }
  .contact-list li {
    display: flex; align-items: center; gap: 3px;
    height: 18px; color: var(--text-muted); font-size: 14.5px;
  }
  .contact-list svg { width: 14px; height: 14px; flex: none; }

  .social-rule { position: absolute; left: 39px; top: 237px; width: 397px; height: 1px; background: var(--rule); }
  .social-icons { position: absolute; left: 218px; top: 228px; display: flex; gap: 4px; }
  .social-icons span { width: 18px; height: 18px; border-radius: 50%; background: var(--gold); display: block; }
  .social-handle {
    position: absolute; left: 0; width: 476px; top: 247px;
    text-align: center; color: var(--text-muted); font-size: 15px;
  }

  .services { position: absolute; left: 266px; top: 86px; list-style: none; }
  .services li {
    display: flex; align-items: center; gap: 4px;
    height: 17.2px; color: var(--text-light); font-size: 14.5px; text-transform: uppercase;
  }
  .services li::before {
    content: ""; width: 7px; height: 7px; border-radius: 50%; background: var(--gold); flex: none;
  }
  .tagline {
    position: absolute; left: 0; width: 476px; top: 239px;
    text-align: center; color: var(--gold); font-size: 15px; font-weight: 500; text-transform: uppercase;
  }
</style>
</head>
<body>

<section class="card card--front" aria-label="Business card front">
  <div class="brand"><span class="brand__dot"></span>LUCKY HARBOUR</div>
  <div class="divider"></div>
  <h1 class="contact-name">ROB KENDALL</h1>
  <p class="contact-role">Director</p>
  <ul class="contact-list">
    <li>
      <svg viewBox="0 0 14 14" aria-hidden="true"><circle cx="7" cy="7" r="7" fill="var(--gold)"/><path d="M3.5 6.2c0-1.6 1.6-2.5 3.5-2.5s3.5.9 3.5 2.5l-1.5.3-.3-1.2H5.3l-.3 1.2zM4.5 7h5l.8 3H3.7z" fill="var(--icon-ink)"/></svg>
      1300 482 617
    </li>
    <li>
      <svg viewBox="0 0 14 14" aria-hidden="true"><circle cx="7" cy="7" r="7" fill="var(--gold)"/><rect x="4.6" y="2.8" width="4.8" height="8.4" rx="0.8" fill="var(--icon-ink)"/><rect x="5.4" y="3.8" width="3.2" height="5.4" fill="var(--gold)"/></svg>
      0433 728 591
    </li>
    <li>
      <svg viewBox="0 0 14 14" aria-hidden="true"><circle cx="7" cy="7" r="7" fill="var(--gold)"/><rect x="3.2" y="4.3" width="7.6" height="5.4" fill="var(--icon-ink)"/><path d="M3.4 4.6 7 7.4l3.6-2.8" stroke="var(--gold)" stroke-width="0.9" fill="none"/></svg>
      info@luckyharbour.com.au
    </li>
    <li>
      <svg viewBox="0 0 14 14" aria-hidden="true"><circle cx="7" cy="7" r="7" fill="var(--gold)"/><circle cx="7" cy="7" r="3.8" fill="none" stroke="var(--icon-ink)" stroke-width="1.1"/><path d="M3.2 7h7.6M7 3.2c-1.6 2.2-1.6 5.4 0 7.6M7 3.2c1.6 2.2 1.6 5.4 0 7.6" stroke="var(--icon-ink)" stroke-width="0.9" fill="none"/></svg>
      www.luckyharbour.com.au
    </li>
  </ul>
  <div class="social-rule"></div>
  <div class="social-icons" aria-label="Social profiles"><span></span><span></span></div>
  <p class="social-handle">@luckyharbourevents</p>
</section>

<section class="card card--back" aria-label="Business card back">
  <div class="brand"><span class="brand__dot"></span>LUCKY HARBOUR</div>
  <div class="divider"></div>
  <ul class="services">
    <li>Corporate Events</li>
    <li>Private Parties</li>
    <li>Poker Tournaments</li>
    <li>Fundraising</li>
    <li>Props &amp; Theming</li>
    <li>Photo Booth</li>
    <li>Horse Racing Events</li>
  </ul>
  <p class="tagline">Australia’s #1 Fun Casino Specialists</p>
</section>

</body>
</html>
```